Elegant Lumocrest Rentals DL flyer

We run a Lumocrest Rentals business - this will be used as a business card as well.

our website is lumocrestrentals.com.au

Front page it sour logo which is attached website details - on the front it needs to say wedding and event hire needs etc..

on the back we will have a spot for 4 products but we want to say there is more so check our the website

A background in the flyer only for example like this would be good http://tapestrova.com/dark-backdrop-image_4726.html

Wedding

Must have
• nice background elegant in style pink and black is the colours

```html
<!DOCTYPE html>
<html lang="en">
<head>
<meta charset="utf-8">
<title>Lumocrest Rentals – DL Flyer</title>
<link rel="stylesheet" href="https://fonts.googleapis.com/css2?family=Great+Vibes&display=swap">
<style>
  :root {
    --ink-black: #121212;
    --ink-deep: #1d1d1d;
    --ink-mid: #2a2a2a;
    --petal-pink: #e0198f;
    --petal-light: #f06ab8;
    --paper-white: #ececec;
    --frame-white: #ffffff;
    --product-grey: #e4e4e4;
    --product-shadow: #c9c9c9;
    --script: "Great Vibes", cursive;
  }
  * { box-sizing: border-box; margin: 0; padding: 0; }
  html, body {
    width: 1200px; height: 1200px; overflow: hidden;
    background: var(--ink-black);
  }
  .flyer {
    position: relative; width: 1200px; height: 1200px; overflow: hidden;
    font-family: var(--script); color: var(--paper-white);
  }
  .backdrop {
    position: absolute; inset: 0;
    background: radial-gradient(ellipse at 50% 35%, var(--ink-mid) 0%, var(--ink-deep) 45%, var(--ink-black) 100%);
  }
  .fold-line {
    position: absolute; left: 0; right: 0; top: 593px;
    border-top: 3px dashed var(--paper-white);
  }
  .text { position: absolute; white-space: nowrap; text-shadow: 0 2px 4px rgba(0,0,0,.7); }

  /* front */
  .brand-dot {
    position: absolute; left: 510px; top: 90px; width: 180px; height: 180px;
    border-radius: 50%;
    background: radial-gradient(circle at 50% 35%, var(--petal-light), var(--petal-pink) 70%);
  }
  .brand-name--front { left: 0; right: 0; top: 285px; text-align: center; font-size: 104px; line-height: 1; }
  .web-address--front { left: 0; right: 0; top: 522px; text-align: center; font-size: 38px; }
  .tagline--corner {
    left: 930px; top: 90px; font-size: 32px; line-height: 1.5; text-align: center;
    transform: rotate(55deg); transform-origin: left top;
  }

  /* back */
  .tagline--back { left: 20px; width: 290px; top: 640px; text-align: center; font-size: 34px; line-height: 1.6; }
  .phone-block { left: 900px; width: 290px; top: 640px; text-align: center; font-size: 34px; line-height: 1.6; }
  .brand-dot--small {
    position: absolute; left: 563px; top: 625px; width: 74px; height: 74px; border-radius: 50%;
    background: radial-gradient(circle at 50% 35%, var(--petal-light), var(--petal-pink) 70%);
  }
  .brand-name--back { left: 0; right: 0; top: 705px; text-align: center; font-size: 32px; }

  .product-row { position: absolute; top: 774px; left: 48px; display: flex; gap: 76px; }
  .product-frame {
    width: 220px; height: 302px; background: var(--frame-white);
    border-radius: 26px; padding: 14px;
    box-shadow: 0 0 0 6px var(--ink-black), 0 0 0 9px var(--frame-white);
  }
  .product-photo {
    width: 100%; height: 100%; border-radius: 14px;
    background: radial-gradient(ellipse at 50% 55%, var(--product-grey), var(--frame-white) 75%);
    border: 1px solid var(--product-shadow);
  }
  .closing-line { left: 0; right: 0; top: 1110px; text-align: center; font-size: 46px; }
</style>
</head>
<body>
<main class="flyer">
  <div class="backdrop" role="img" aria-label="Dark black damask patterned background"></div>

  <section class="front-panel">
    <div class="brand-dot"></div>
    <h1 class="text brand-name--front">Lumocrest Rentals</h1>
    <p class="text tagline--corner">Wedding and Event<br>hire needs!</p>
    <p class="text web-address--front">www.lumocrestrentals.com.au</p>
  </section>

  <div class="fold-line"></div>

  <section class="back-panel">
    <p class="text tagline--back">Wedding and Event<br>hire needs!</p>
    <div class="brand-dot--small"></div>
    <p class="text brand-name--back">Lumocrest Rentals</p>
    <p class="text phone-block">Phone Number:<br>040 555 0192</p>

    <div class="product-row">
      <div class="product-frame"><div class="product-photo" role="img" aria-label="White folding event chair"></div></div>
      <div class="product-frame"><div class="product-photo" role="img" aria-label="Beige market umbrella on a stand"></div></div>
      <div class="product-frame"><div class="product-photo" role="img" aria-label="Glowing white LED cube seat"></div></div>
      <div class="product-frame"><div class="product-photo" role="img" aria-label="Black bar stool with metal legs"></div></div>
    </div>

    <p class="text closing-line">Check our website for more products!</p>
  </section>
</main>
</body>
</html>
```